Business Card Re-Design/Update

We'd like to update out business cards. I've included our current "Style guide" which has the colour scheme of the organisation in it. I've also included the branding files with logos etc in them.

I've also included a copy of one of our existing cards so that you can see how ugly/dated they look. I'd like a fresh modern corporate look.

Target Market(s)

These are for our clients, potential clients, industry contacts - like all business cards

Contact Information for Business Card

Name
Position
Company Address - Level 1, 47 Fernby Street, Carlow Qld 4072
Direct Phone
mobile
Email
Website -www.korvalit.com.au
Logo

Colors

Designer to choose colors to be used in the design.

Requirements
Must have
• Main Logo
• Cards will need to be editable to be able to personalize them for each new employee.
Nice to have
• The MapOut, ShipWell, KeepSteady would be okay to have if they can be sensibly and professionally added to the look without detracting from the main imagery.
• Maybe they could go on the back of the card? will leave this to your creative discretion as to whether/where they fit.
Should not have
• Should not have decorative or script fonts

```html
<!DOCTYPE html>
<html lang="en">
<head>
<meta charset="utf-8">
<title>Korvalit Business Card</title>
<link rel="stylesheet" href="https://fonts.googleapis.com/css2?family=Montserrat:wght@500;600&family=Arimo:wght@400&display=swap">
<style>
  :root {
    --backdrop: #2a2a2b;
    --card: #1e1f21;
    --card-back: #1b1c1e;
    --pattern: #232426;
    --brand-red: #e3161d;
    --wordmark: #5c5d60;
    --text-light: #c9cacc;
    --rule: #6e7275;
  }
  * { margin: 0; padding: 0; box-sizing: border-box; }
  html, body { width: 1200px; height: 1108px; overflow: hidden; }
  body {
    background: var(--backdrop);
    font-family: "Arimo", Arial, sans-serif;
    position: relative;
  }
  .card {
    position: absolute;
    top: 194px;
    width: 460px;
    height: 720px;
    border-radius: 22px;
    overflow: hidden;
  }
  .card-front { left: 100px; background: var(--card); }
  .card-back { left: 640px; background: var(--card-back); }

  .brand-square {
    display: block;
    width: 64px; height: 64px;
    background: var(--brand-red);
    margin: 110px auto 0;
  }
  .wordmark {
    font-family: "Montserrat", Arial, sans-serif;
    font-weight: 600;
    color: var(--wordmark);
    font-size: 64px;
    letter-spacing: -1px;
    text-align: center;
    line-height: 1;
    margin-top: 18px;
  }
  .person-name {
    font-family: "Montserrat", Arial, sans-serif;
    font-weight: 600;
    color: var(--brand-red);
    font-size: 24px;
    text-align: center;
    text-transform: uppercase;
    margin-top: 48px;
  }
  .person-role {
    color: var(--text-light);
    font-size: 19px;
    text-align: center;
    margin-top: 4px;
  }
  .icon-rule {
    display: flex;
    align-items: center;
    gap: 8px;
    margin: 18px 56px 0;
  }
  .icon-rule .line { flex: 1; height: 1px; background: var(--rule); }
  .icon-rule svg { display: block; }
  .contact-list {
    list-style: none;
    color: var(--text-light);
    font-size: 19px;
    line-height: 25px;
    text-align: center;
    margin-top: 12px;
  }
  .divider { height: 1px; background: var(--rule); margin: 12px 70px 0; }
  .address {
    color: var(--text-light);
    font-size: 19px;
    line-height: 25px;
    text-align: center;
    margin-top: 12px;
  }

  .back-pattern {
    position: absolute;
    inset: 0 0 190px 0;
    background: linear-gradient(160deg, var(--pattern), var(--card-back));
  }
  .back-brand {
    position: absolute;
    left: 60px; bottom: 96px;
    display: flex;
    align-items: center;
    gap: 14px;
  }
  .back-brand .brand-square { width: 46px; height: 46px; margin: 0; }
  .back-brand .wordmark { font-size: 52px; margin: 0; }
</style>
</head>
<body>

<section class="card card-front">
  <span class="brand-square"></span>
  <div class="wordmark">korvalit</div>
  <h1 class="person-name">Maren Whitlock</h1>
  <p class="person-role">Business Development Manager</p>

  <div class="icon-rule">
    <span class="line"></span>
    <svg width="124" height="22" viewBox="0 0 124 22" aria-hidden="true">
      <g fill="#e3161d">
        <rect x="0" y="0" width="22" height="22" rx="2"/>
        <rect x="25" y="0" width="22" height="22" rx="2"/>
        <rect x="50" y="0" width="22" height="22" rx="2"/>
        <rect x="75" y="0" width="22" height="22" rx="2"/>
        <rect x="100" y="0" width="22" height="22" rx="2"/>
      </g>
      <g fill="none" stroke="#1e1f21" stroke-width="1.8" stroke-linecap="round" stroke-linejoin="round">
        <path d="M6 5c0 6 5 11 11 11l1-3-3-1-1 1c-2-1-4-3-5-5l1-1-1-3z"/>
        <rect x="32" y="4" width="8" height="14" rx="1.5"/>
        <path d="M55 9h12v7H55zM57 9V5h8v4M57 13h8"/>
        <rect x="79" y="6" width="14" height="10"/>
        <path d="M79 6l7 6 7-6"/>
        <circle cx="111" cy="11" r="6"/>
        <path d="M105 11h12M111 5c-3 3-3 9 0 12M111 5c3 3 3 9 0 12"/>
      </g>
    </svg>
    <span class="line"></span>
  </div>

  <ul class="contact-list">
    <li>+61 (0)412 555 018</li>
    <li>+61 (0)7 3555 0142</li>
    <li>+61 (0)7 3555 0147</li>
    <li>mwhitlock@korvalit.com.au</li>
    <li>www.korvalit.com.au</li>
  </ul>
  <div class="divider"></div>
  <p class="address">Level 1, 47 Fernby Street<br>Carlow Qld 4072</p>
</section>

<section class="card card-back">
  <div class="back-pattern" role="img" aria-label="Faint repeating brand mark pattern across the back of the card"></div>
  <div class="back-brand">
    <span class="brand-square"></span>
    <span class="wordmark">korvalit</span>
  </div>
</section>

</body>
</html>
```